Oriel Photography Business Card

I need a business card designed for a photography business based in Perth, Western Australia called Oriel Photography.

We specialise in wedding, event photography and portrait photography.

The business card must borrow the style of the attached logo.

The hex codes for the colours in the logo are:
#ED1D85 - Pink
#89C23E - Green
#37282F - Black

The name on the card will be:
Name: Tobrian
Phone: 0417395268
Website: www.orielphotography.example.com.au
Facebook: orielphotography

I am open and happy to accept creative concepts.

I’d like some space at the back for writing notes and appointment details.

```html
<!DOCTYPE html>
<html lang="en">
<head>
<meta charset="utf-8">
<title>Oriel Photography – Business Card</title>
<link rel="stylesheet" href="https://fonts.googleapis.com/css2?family=Arimo:wght@400;700&display=swap">
<style>
  :root {
    --pink: #ED1D85;
    --green: #89C23E;
    --lime: #9BE51E;
    --black: #0a0a0a;
    --ink: #37282F;
    --grey-text: #3a3a3a;
    --paper: #ffffff;
    --backdrop: #eceae6;
  }
  * { box-sizing: border-box; margin: 0; padding: 0; }
  html, body { width: 1200px; height: 1000px; overflow: hidden; }
  body {
    background: var(--backdrop);
    font-family: "Arimo", Arial, sans-serif;
    position: relative;
  }
  .card {
    position: absolute;
    left: 250px;
    width: 700px;
    height: 400px;
    overflow: hidden;
    box-shadow: 0 6px 18px rgba(0,0,0,.18);
  }
  .card--front { top: 70px; background: var(--black); }
  .card--back { top: 520px; background: var(--paper); }

  .corner { position: absolute; width: 26px; height: 20px; border-color: var(--lime); border-style: solid; border-width: 0; }
  .corner--tl { top: 28px; left: 32px; border-top-width: 2px; border-left-width: 2px; }
  .corner--tr { top: 28px; right: 32px; border-top-width: 2px; border-right-width: 2px; }
  .corner--bl { bottom: 28px; left: 32px; border-bottom-width: 2px; border-left-width: 2px; }
  .corner--br { bottom: 28px; right: 32px; border-bottom-width: 2px; border-right-width: 2px; }
  .card--front .corner--bl, .card--front .corner--br { bottom: 88px; }

  .brand-mark {
    position: absolute; left: 50%; width: 74px; height: 74px;
    margin-left: -37px; border-radius: 50%; background: var(--pink);
  }
  .card--front .brand-mark { top: 102px; }
  .card--back .brand-mark { top: 40px; }

  .wordmark {
    position: absolute; left: 0; right: 0; text-align: center;
    font-size: 15px; letter-spacing: 9px; text-transform: uppercase;
  }
  .card--front .wordmark { top: 200px; color: var(--grey-text); }
  .card--back .wordmark { top: 126px; color: var(--ink); }

  .services {
    position: absolute; left: 0; right: 0; top: 258px; text-align: center;
    color: var(--grey-text); font-size: 15px; letter-spacing: 1.5px;
  }
  .accent-rule { position: absolute; left: 0; right: 0; top: 312px; height: 3px; background: var(--pink); }
  .accent-band { position: absolute; left: 0; right: 0; top: 315px; bottom: 0; background: var(--lime); }

  .divider { position: absolute; left: 0; right: 0; }
  .divider--dark { top: 154px; height: 4px; background: var(--ink); }
  .divider--green { top: 160px; height: 4px; background: var(--lime); }
  .divider--notes { top: 250px; height: 3px; background: var(--ink); }
  .divider--notes-green { top: 255px; height: 3px; background: var(--lime); }

  .contact {
    position: absolute; right: 52px; top: 172px; text-align: right;
    font-size: 15px; line-height: 18px;
  }
  .contact__name { color: var(--pink); font-weight: 700; font-size: 19px; line-height: 24px; }
  .contact__line--pink { color: var(--pink); }
  .contact__line--green { color: var(--lime); }
</style>
</head>
<body>
  <section class="card card--front" aria-label="Business card front">
    <span class="corner corner--tl"></span>
    <span class="corner corner--tr"></span>
    <span class="corner corner--bl"></span>
    <span class="corner corner--br"></span>
    <span class="brand-mark"></span>
    <p class="wordmark">Oriel Photography</p>
    <p class="services">Wedding Event Photography Portrait Photography</p>
    <div class="accent-rule"></div>
    <div class="accent-band"></div>
  </section>

  <section class="card card--back" aria-label="Business card back">
    <span class="corner corner--tl"></span>
    <span class="corner corner--tr"></span>
    <span class="corner corner--bl"></span>
    <span class="corner corner--br"></span>
    <span class="brand-mark"></span>
    <p class="wordmark">Oriel Photography</p>
    <div class="divider divider--dark"></div>
    <div class="divider divider--green"></div>
    <div class="contact">
      <p class="contact__name">Tobrian</p>
      <p class="contact__line--pink">P: 0417395268</p>
      <p class="contact__line--pink">W: www.orielphotography.example.com.au</p>
      <p class="contact__line--green">f: facebook/orielphotography</p>
    </div>
    <div class="divider divider--notes"></div>
    <div class="divider divider--notes-green"></div>
  </section>
</body>
</html>
```